Web Developer Needs a Business Card Design

I need a personal business card design that represents me as a web developer for potential employers. I would like the background to be a dark color on the front for contrast with my logo and name. The back will have all my information along with a smaller version of the logo. I want something with a modern look and feel, not too conservative. This will be used for potential employers and freelance work.

Industry/Entity Type

Business

Contact Information for Business Card

Front should have my logo and name. The back should have all my personal information which would include: name: Tom Varulek, phone: 570-614-3098, email: tomvarulek@quillbox.net, website url: www.tomvarulek.net, logo, web developer.

Font styles to use
Sans Serif

Requirements
Must have
• Must include my logo. The color palette base color will be the logo color.

```html
<!DOCTYPE html>
<html lang="en">
<head>
<meta charset="utf-8">
<title>Tom Varulek — Business Card</title>
<link rel="stylesheet" href="https://fonts.googleapis.com/css2?family=Open+Sans:wght@400;700&display=swap">
<style>
  :root {
    --teal: #6cc7b2;
    --ink: #0a0a0a;
    --silver: #c9c9c9;
    --white: #ffffff;
    --stage: #e6e6e4;
    --card-w: 600px;
    --card-h: 343px;
  }
  * { box-sizing: border-box; margin: 0; padding: 0; }
  html, body {
    width: 1200px; height: 900px; overflow: hidden;
    background: var(--stage);
    font-family: "Open Sans", Arial, sans-serif;
  }
  .stage {
    position: relative; width: 1200px; height: 900px;
    display: flex; flex-direction: column; align-items: center; justify-content: center; gap: 50px;
  }
  .card {
    position: relative; width: var(--card-w); height: var(--card-h);
    background: var(--teal); overflow: hidden;
    box-shadow: 0 6px 18px rgba(0,0,0,0.18);
  }
  .card svg.shapes { position: absolute; inset: 0; width: 100%; height: 100%; }

  /* Front */
  .front__mark {
    position: absolute; left: 20px; top: 120px; width: 230px;
    color: var(--white); font-weight: 700; font-size: 30px; line-height: 1.1;
    text-align: center;
  }
  .front__name {
    position: absolute; right: 40px; bottom: 40px;
    color: var(--white); font-weight: 700; font-size: 26px; letter-spacing: 0.5px;
  }

  /* Back */
  .back__mark {
    position: absolute; left: 76px; top: 120px; width: 170px;
    color: var(--teal); font-weight: 700; font-size: 22px; line-height: 1.15;
    text-align: center;
  }
  .back__identity {
    position: absolute; right: 36px; top: 40px; text-align: right; color: var(--white);
  }
  .back__name { font-weight: 700; font-size: 20px; letter-spacing: 0.4px; }
  .back__title { font-size: 16px; margin-top: 2px; }
  .back__contacts {
    position: absolute; right: 30px; bottom: 34px; list-style: none;
    color: var(--white); font-size: 17px; line-height: 1.5; text-align: right;
  }
  .back__contacts li { display: flex; align-items: center; justify-content: flex-end; gap: 10px; }
  .back__contacts svg { width: 13px; height: 13px; flex: none; }
</style>
</head>
<body>
<main class="stage">

  <section class="card card--front" aria-label="Card front">
    <svg class="shapes" viewBox="0 0 600 343" aria-hidden="true">
      <circle cx="110" cy="120" r="228" fill="none" stroke="var(--white)" stroke-width="14"/>
      <circle cx="110" cy="120" r="200" fill="var(--white)" opacity="0"/>
    </svg>
    <div class="front__mark">Tom<br>Varulek</div>
    <p class="front__name">Tom Varulek</p>
  </section>

  <section class="card card--back" aria-label="Card back">
    <svg class="shapes" viewBox="0 0 600 343" aria-hidden="true">
      <path d="M0 0 H300 C 335 70 330 230 235 343 H0 Z" fill="var(--silver)"/>
      <path d="M0 0 H284 C 318 70 306 228 212 343 H0 Z" fill="var(--white)"/>
      <path d="M0 0 H272 C 300 80 290 230 196 343 H0 Z" fill="var(--ink)"/>
      <circle cx="161" cy="150" r="92" fill="none" stroke="var(--teal)" stroke-width="9"/>
    </svg>
    <div class="back__mark">Tom<br>Varulek</div>

    <div class="back__identity">
      <p class="back__name">Tom Varulek</p>
      <p class="back__title">Front-End Developer</p>
    </div>

    <ul class="back__contacts">
      <li>570-614-3098
        <svg viewBox="0 0 24 24" aria-hidden="true"><path fill="var(--white)" d="M6.6 10.8a15.1 15.1 0 0 0 6.6 6.6l2.2-2.2a1 1 0 0 1 1-.25 11.4 11.4 0 0 0 3.6.57 1 1 0 0 1 1 1V20a1 1 0 0 1-1 1A17 17 0 0 1 3 4a1 1 0 0 1 1-1h3.5a1 1 0 0 1 1 1c0 1.25.2 2.45.57 3.57a1 1 0 0 1-.25 1z"/></svg>
      </li>
      <li>tomvarulek@quillbox.net
        <svg viewBox="0 0 24 24" aria-hidden="true"><rect x="2" y="5" width="20" height="14" fill="var(--white)"/><path d="M2 5 L12 13 L22 5" fill="none" stroke="var(--teal)" stroke-width="1.8"/></svg>
      </li>
      <li>www.tomvarulek.net
        <svg viewBox="0 0 24 24" aria-hidden="true"><g fill="none" stroke="var(--white)" stroke-width="2"><circle cx="12" cy="12" r="9"/><ellipse cx="12" cy="12" rx="4" ry="9"/><path d="M3 12h18"/></g></svg>
      </li>
    </ul>
  </section>

</main>
</body>
</html>
```